Redesign of business card for Cedar Ridge Mechanical

We are looking for a new design for our business cards for Cedar Ridge Mechanical. We are a plumbing & HVAC construction company, operating on the West Coast of Canada and USA. Logo attached.
Industry/Entity Type
Construction - Plumbing & HVAC
Contact Information for Business Card
Name, address, phone numbers, email, website address
Look and feel
Each slider illustrates characteristics of the customer's brand and the style your logo design should communicate.

```html
<!DOCTYPE html>
<html lang="en">
<head>
<meta charset="UTF-8">
<title>Cedar Ridge Mechanical — Business Card</title>
<link href="https://fonts.googleapis.com/css2?family=Montserrat:wght@400;800&display=swap" rel="stylesheet">
<style>
  :root {
    --backdrop: #2b2b2e;
    --card-black: #0c0c0c;
    --mark-on-black: #2e2e2e;
    --card-white: #ffffff;
    --ink: #0a0a0a;
    --ink-soft: #444444;
  }
  * { margin: 0; padding: 0; box-sizing: border-box; }
  html, body { width: 1200px; height: 913px; overflow: hidden; }
  body {
    background: var(--backdrop);
    font-family: "Montserrat", sans-serif;
    position: relative;
  }
  .card {
    position: absolute;
    width: 560px;
    height: 320px;
    border-radius: 22px;
    overflow: hidden;
  }
  /* Front side */
  .card-front {
    left: 70px;
    top: 100px;
    background: var(--card-black);
    display: flex;
    align-items: center;
    justify-content: center;
    gap: 18px;
  }
  .card-front .brand-square {
    width: 38px; height: 38px;
    background: var(--mark-on-black);
  }
  .card-front .brand-name {
    color: var(--mark-on-black);
    font-weight: 800;
    font-size: 30px;
    line-height: 1.1;
    text-transform: uppercase;
    letter-spacing: 1px;
  }
  /* Back side */
  .card-back {
    left: 570px;
    top: 490px;
    background: var(--card-white);
    color: var(--ink);
  }
  .back-brand {
    position: absolute;
    left: 30px; top: 28px;
    display: flex; align-items: center; gap: 10px;
  }
  .back-brand .brand-square { width: 20px; height: 20px; background: var(--ink); }
  .back-brand .brand-name {
    font-weight: 800; font-size: 14px; line-height: 1.15;
    text-transform: uppercase; letter-spacing: .5px;
  }
  .edge-tab {
    position: absolute; left: 0; top: 110px;
    width: 10px; height: 50px; background: var(--ink);
  }
  .contact {
    position: absolute; left: 30px; top: 112px;
  }
  .contact .person { font-weight: 800; font-size: 22px; letter-spacing: .5px; text-transform: uppercase; }
  .contact .role { font-size: 13px; color: var(--ink-soft); margin: 4px 0 14px; }
  .contact .address { font-size: 13px; color: var(--ink-soft); line-height: 1.5; margin-bottom: 12px; }
  .contact ul { list-style: none; }
  .contact li {
    display: flex; align-items: center; gap: 8px;
    font-size: 13px; color: var(--ink-soft); line-height: 1.75;
  }
  .contact svg { width: 12px; height: 12px; fill: var(--ink); }
  .back-mark {
    position: absolute; right: 36px; top: 40px;
    display: flex; align-items: center; gap: 16px;
  }
  .back-mark .brand-square { width: 48px; height: 48px; background: var(--ink); }
  .back-mark .brand-name {
    font-weight: 800; font-size: 30px; line-height: 1.1;
    text-transform: uppercase;
  }
</style>
</head>
<body>

  <section class="card card-front" aria-label="Card front">
    <span class="brand-square"></span>
    <p class="brand-name">Cedar Ridge<br>Mechanical</p>
  </section>

  <section class="card card-back" aria-label="Card back">
    <div class="back-brand">
      <span class="brand-square"></span>
      <p class="brand-name">Cedar Ridge<br>Mechanical</p>
    </div>

    <span class="edge-tab"></span>

    <div class="contact">
      <p class="person">Daniel Hayes</p>
      <p class="role">Managing Director</p>
      <p class="address">Your address, City<br>State, Zip 1234</p>
      <ul>
        <li><svg viewBox="0 0 24 24"><path d="M6.6 10.8a15 15 0 0 0 6.6 6.6l2.2-2.2a1 1 0 0 1 1-.25 11.4 11.4 0 0 0 3.6.57 1 1 0 0 1 1 1V20a1 1 0 0 1-1 1A17 17 0 0 1 3 4a1 1 0 0 1 1-1h3.5a1 1 0 0 1 1 1c0 1.25.2 2.45.57 3.57a1 1 0 0 1-.25 1z"/></svg>604 555 0182</li>
        <li><svg viewBox="0 0 24 24"><path d="M2 5h20v14H2zm2 2v.5l8 5 8-5V7zm0 2.8V17h16V9.8l-8 5z"/></svg>info@cedarridgemech.com</li>
        <li><svg viewBox="0 0 24 24"><path d="M12 2a10 10 0 1 0 0 20 10 10 0 0 0 0-20zm6.9 6h-3a15 15 0 0 0-1.3-3.9A8 8 0 0 1 18.9 8zM12 4c.8 1.2 1.5 2.5 1.9 4h-3.8c.4-1.5 1.1-2.8 1.9-4zM4.3 14a8 8 0 0 1 0-4h3.4a16 16 0 0 0 0 4zm.8 2h3a15 15 0 0 0 1.3 3.9A8 8 0 0 1 5.1 16zm3-8h-3a8 8 0 0 1 4.3-3.9A15 15 0 0 0 8.1 8zM12 20c-.8-1.2-1.5-2.5-1.9-4h3.8c-.4 1.5-1.1 2.8-1.9 4zm2.3-6H9.7a14 14 0 0 1 0-4h4.6a14 14 0 0 1 0 4zm.3 5.9a15 15 0 0 0 1.3-3.9h3a8 8 0 0 1-4.3 3.9zm1.7-5.9a16 16 0 0 0 0-4h3.4a8 8 0 0 1 0 4z"/></svg>www.cedarridgemech.com</li>
      </ul>
    </div>

    <div class="back-mark">
      <span class="brand-square"></span>
      <p class="brand-name">Cedar Ridge<br>Mechanical</p>
    </div>
  </section>

</body>
</html>
```